Communication and Marketing agency needs a new presentation card

We are a group of communication and marketing agencies specialized in companies that are in the logistics and industrial sector. The head agency is TELVANO Grupo and the group consists of 4 agencies: TELVANO Media, TELVANO Digital, TELVANO Research and DifundeEnPantalla. We hace 4 offices in Spain (Madrid, Barcelona, Valencia and Murcia). We are looking for a clean and attractive design that transmits our experience, brand presence in the market and knowledge to those who receive the card.It has to maintain the colors of the logo that is attached.
Target Market(s)
logistics and industrial sector
Marketing department
Contact Information for Business Card
Clean and attractive design

```html
<!DOCTYPE html>
<html lang="es">
<head>
<meta charset="utf-8">
<title>TELVANO Grupo – Tarjeta de presentación</title>
<link rel="stylesheet" href="https://fonts.googleapis.com/css2?family=Roboto+Condensed:wght@300;400;700&display=swap">
<style>
  :root {
    --page: #ffffff;
    --card-dark: #000000;
    --card-light: #ffffff;
    --ink-light: #ffffff;
    --brand-red: #b01f2c;
    --brand-grey: #4a4a4a;
    --shadow: rgba(0, 0, 0, 0.28);
  }
  * { margin: 0; padding: 0; box-sizing: border-box; }
  html, body {
    width: 1200px; height: 1200px; overflow: hidden;
    background: var(--page);
    font-family: "Roboto Condensed", sans-serif;
  }
  .canvas { position: relative; width: 1200px; height: 1200px; }

  .card {
    position: absolute; top: 272px;
    width: 379px; height: 664px;
    box-shadow: 8px 10px 18px var(--shadow);
  }
  .card--front { left: 171px; background: var(--card-dark); color: var(--ink-light); }
  .card--back { left: 657px; background: var(--card-light); }

  /* Front */
  .holder { position: absolute; top: 56px; width: 100%; text-align: center; }
  .holder__name { font-size: 29px; font-weight: 400; line-height: 34px; }
  .holder__role { font-size: 27px; font-weight: 300; line-height: 40px; }

  .contact-frame {
    position: absolute; left: 51px; top: 164px;
    width: 277px; height: 455px;
    border: 2px solid var(--ink-light);
    box-shadow: 0 0 26px rgba(255, 255, 255, 0.35);
  }
  .contact { position: absolute; top: 30px; width: 100%; text-align: center; list-style: none; }
  .contact__line { font-size: 24px; font-weight: 300; line-height: 32px; }
  .contact__line--social { display: flex; justify-content: center; align-items: center; gap: 6px; }
  .social-dot { width: 20px; height: 20px; border-radius: 50%; background: var(--ink-light); flex: none; }
  .contact__web { margin-top: 14px; font-size: 24px; font-weight: 400; }

  .brand-front {
    position: absolute; right: 30px; top: 310px;
    text-align: right; color: var(--ink-light);
    font-weight: 300; line-height: 0.95;
  }
  .brand-front__name { display: block; font-size: 50px; letter-spacing: 3px; }
  .brand-front__unit { display: block; font-size: 30px; }

  /* Back */
  .agency-panel {
    position: absolute; left: 50px; top: 45px;
    width: 279px; height: 431px;
    background: var(--card-light);
    box-shadow: 0 0 22px rgba(0, 0, 0, 0.12);
  }
  .agency {
    position: absolute; right: 72px;
    text-align: right; font-weight: 400; line-height: 0.95;
  }
  .agency__name { display: block; font-size: 28px; letter-spacing: 2px; }
  .agency__unit { display: block; font-size: 17px; }
  .agency--digital { top: 46px; color: var(--brand-grey); }
  .agency--media { top: 146px; color: var(--brand-red); }
  .agency--research { top: 241px; color: var(--brand-grey); }
  .agency--video {
    top: 340px; right: auto; left: 0; width: 100%;
    text-align: center; color: var(--brand-red);
    font-size: 24px; letter-spacing: 1px;
  }

  .brand-back {
    position: absolute; right: 45px; top: 526px;
    text-align: right; color: var(--brand-red);
    font-weight: 400; line-height: 0.95;
  }
  .brand-back__name { display: block; font-size: 62px; letter-spacing: 4px; }
  .brand-back__unit { display: block; font-size: 38px; }
</style>
</head>
<body>
<main class="canvas">
  <section class="card card--front" aria-label="Anverso de la tarjeta">
    <header class="holder">
      <h1 class="holder__name">Andrés Vallejo</h1>
      <p class="holder__role">Director</p>
    </header>
    <div class="contact-frame">
      <ul class="contact">
        <li class="contact__line">T. 910 472 158</li>
        <li class="contact__line">M. 655 219 743</li>
        <li class="contact__line">avallejo@telvano.es</li>
        <li class="contact__line contact__line--social"><span class="social-dot" aria-hidden="true"></span>andresvallejo</li>
        <li class="contact__web">www.telvano.es</li>
      </ul>
      <p class="brand-front">
        <span class="brand-front__name">TELVANO</span>
        <span class="brand-front__unit">Grupo</span>
      </p>
    </div>
  </section>

  <section class="card card--back" aria-label="Reverso de la tarjeta">
    <div class="agency-panel">
      <p class="agency agency--digital"><span class="agency__name">TELVANO</span><span class="agency__unit">Digital</span></p>
      <p class="agency agency--media"><span class="agency__name">TELVANO</span><span class="agency__unit">Media</span></p>
      <p class="agency agency--research"><span class="agency__name">TELVANO</span><span class="agency__unit">Research</span></p>
      <p class="agency agency--video">DifundeEnPantalla</p>
    </div>
    <p class="brand-back">
      <span class="brand-back__name">TELVANO</span>
      <span class="brand-back__unit">Grupo</span>
    </p>
  </section>
</main>
</body>
</html>
```